Technical Communications firm needs an article turned into a white paper

We want to redesign a 3-part blog series into a white paper that we can print for a conference. I've consolidated the three posts into the attached Word document.

We are looking for a light, easy to read design. Good use of graphics to support the message. I've added the graphics we used in the original post.

You can view them at
http://www.brightquillpages.com/blog/are-you-satisfied-with-your-dita-solution/

Target Market(s)

Product managers from High-tech, Finance, and Medical industries.

Industry/Entity Type

Information Technology

Colors

Designer to choose colors to be used in the design.

Requirements
Must have
• Must be modern, light, easy to read and slick design. Try to incorporate the graphics provided, but feel free to add more. Must retain the lists and tables.
• Must align with our website/brand.
• Must be easy to read. So not too busy.
• Please move all footnotes to endnotes. You'll need to rework the numbering.
Nice to have
• Awesome coverpage.
Should not have
• Hokey clipart. Not too heavy or hard to read.

```html
<!DOCTYPE html>
<html lang="en">
<head>
<meta charset="utf-8">
<title>Part 1: Skills Development — White Paper Spread</title>
<link href="https://fonts.googleapis.com/css2?family=Lato:ital,wght@0,400;0,700;1,400&family=Titillium+Web:wght@400;600;700&display=swap" rel="stylesheet">
<style>
  :root{
    --navy:#2a4790;
    --sky:#4d9bd3;
    --heading:#2e4e9e;
    --ink:#3f4248;
    --muted:#6b6f76;
    --rule:#c9ced6;
    --paper:#ffffff;
    --backdrop:#e6e5e2;
    --photo-top:#5e8f70;
    --photo-bottom:#3f6d52;
  }
  *{box-sizing:border-box;margin:0;padding:0}
  html,body{width:1200px;height:804px;overflow:hidden;background:var(--backdrop)}
  body{font-family:"Lato",Arial,sans-serif;color:var(--ink)}
  .spread{position:absolute;left:25px;top:17px;width:1150px;height:770px;display:flex;box-shadow:0 6px 24px rgba(0,0,0,.18)}
  .page{position:relative;width:575px;height:770px;background:var(--paper);overflow:hidden}
  .page--left{border-right:1px solid #dcdcdc}
  .hero-photo{height:250px;background:linear-gradient(180deg,var(--photo-top),var(--photo-bottom))}
  .page-body{padding:0 42px}
  .article-title{font-family:"Titillium Web",Arial,sans-serif;font-weight:600;font-size:23px;color:#3a3d44;margin-top:22px}
  .byline{text-align:right;font-style:italic;font-size:11px;color:var(--muted);margin-top:2px}
  .byline-role{text-align:right;font-style:italic;font-size:8.5px;color:var(--muted);margin-top:8px}
  p.body{font-size:9px;line-height:1.42;margin-top:12px}
  h2.section{font-family:"Titillium Web",Arial,sans-serif;font-weight:700;font-size:15.5px;color:var(--heading);margin-top:14px;line-height:1.2}
  .rank-chart{display:block;margin-top:6px}
  .rank-chart text{font-family:"Lato",Arial,sans-serif;font-size:9px;fill:var(--ink)}
  .footer{position:absolute;left:0;bottom:0;width:100%;height:50px}
  .footer svg{position:absolute;inset:0}
  .footer-contact{position:absolute;bottom:9px;font-size:9.5px;color:#fff;letter-spacing:.2px}
  .footer-page{position:absolute;bottom:22px;font-size:9.5px;color:#fff;letter-spacing:.5px}
  .top-band{position:absolute;right:0;top:0;width:330px;height:44px}
  .top-band span{position:absolute;right:20px;top:10px;font-size:9.5px;color:#fff}
  .page--right .page-body{padding-top:70px}
  .page--right p.body:first-child{margin-top:0}
  .compare{width:100%;border-collapse:collapse;margin-top:12px;font-size:8.5px}
  .compare th{font-family:"Titillium Web",Arial,sans-serif;font-weight:700;font-size:12px;color:#fff;padding:5px 0;text-align:center}
  .compare th.sw{background:var(--navy)}
  .compare th.sm{background:var(--sky)}
  .compare td{border:1px solid var(--rule);padding:4px 6px;line-height:1.25;vertical-align:middle}
  .compare td.tick{width:26px;text-align:center;font-size:10px;color:#555}
  .table-note{font-size:7.5px;font-style:italic;color:#8a8d93;text-align:right;margin-top:3px}
  .checklist{list-style:none;margin-top:8px}
  .checklist li{display:flex;gap:7px;font-size:9px;line-height:1.35;margin-top:6px}
  .checklist svg{flex:0 0 11px;margin-top:1px}
</style>
</head>
<body>
<main class="spread">

  <section class="page page--left">
    <div class="hero-photo" role="img" aria-label="Photo of a puzzled man peeking up at a green chalkboard that reads: What am I supposed to do"></div>
    <div class="page-body">
      <h1 class="article-title">Part 1: Skills Development</h1>
      <p class="byline">By Dana Whitlock</p>
      <p class="byline-role">President of Bright Quill Authoring Solutions Inc.</p>
      <p class="body">This article is part of a series based on the results of a survey of more than 250 technical communication professionals conducted by The Content Corral in 2017 entitled The Structured Authoring Pulse Study[i]. In the survey, almost two-thirds of respondents voiced concerns with their DITA deployment. In our previous article, we introduced the overall results from the survey that pertain to users’ dissatisfaction with their DITA solution. In this article, we examine the top rated issues pertaining to skills development.</p>
      <h2 class="section">Issues related to skills development</h2>
      <p class="body" style="margin-top:6px">The top-ranked reported issues fall under the category of skill development and training. These include</p>
      <svg class="rank-chart" width="490" height="175" viewBox="0 0 490 175" aria-label="Ranked skills development issues">
        <ellipse cx="90" cy="138" rx="78" ry="30" fill="#3d6f98"/>
        <ellipse cx="90" cy="108" rx="78" ry="30" fill="#5599c9"/>
        <ellipse cx="90" cy="78" rx="78" ry="30" fill="#8cc3dc"/>
        <ellipse cx="90" cy="48" rx="78" ry="30" fill="#c2def1"/>
        <g stroke="#b8bcc2" stroke-width="1" fill="#fff">
          <line x1="160" y1="38" x2="290" y2="30"/><circle cx="292" cy="30" r="2.5"/>
          <line x1="165" y1="80" x2="290" y2="70"/><circle cx="292" cy="70" r="2.5"/>
          <line x1="165" y1="112" x2="290" y2="104"/><circle cx="292" cy="104" r="2.5"/>
          <line x1="160" y1="148" x2="290" y2="138"/><circle cx="292" cy="138" r="2.5"/>
        </g>
        <text x="302" y="26">How do I reuse content? Ranked 1st by</text>
        <text x="302" y="38">75% of respondents</text>
        <text x="302" y="66">How do I make DITA do what I want it to</text>
        <text x="302" y="78">do? Ranked 2nd by 69% of respondents</text>
        <text x="302" y="100">Where can I get DITA training? Ranked</text>
        <text x="302" y="112">3rd by 64% of respondents, and</text>
        <text x="302" y="134">How do I create DITA content? Ranked</text>
        <text x="302" y="146">8th by 56% of respondents.</text>
      </svg>
    </div>
    <footer class="footer">
      <svg width="575" height="50" viewBox="0 0 575 50" aria-hidden="true">
        <polygon points="0,28 370,28 382,8 575,8 575,50 0,50" fill="var(--navy)"/>
        <polygon points="0,32 356,32 344,50 0,50" fill="var(--sky)"/>
      </svg>
      <span class="footer-contact" style="left:40px">Phone: +1 (555) 014-2290 &nbsp;|&nbsp; more-info@brightquillpages.com</span>
      <span class="footer-page" style="right:42px">PAGE 10 OF 10</span>
    </footer>
  </section>

  <section class="page page--right">
    <div class="top-band">
      <svg width="330" height="44" viewBox="0 0 330 44" aria-hidden="true">
        <polygon points="0,30 22,30 34,44 330,44 330,0 0,0" fill="var(--navy)"/>
      </svg>
      <span>www.brightquillpages.com</span>
    </div>
    <div class="page-body">
      <p class="body">This problem area is far and away the most pressing obstacle for a successful DITA deployment. Too often authors are left to figure out how to adapt to writing for DITA on their own. Organizations will normally invest in tools training—and may even opt for a short training course to learn about DITA—but they rarely make the effort to train writers how to author modular, structured topics of content designed for reuse. It is easy to overlook this training aspect and assume that writers will naturally adapt to this new way of writing. But, those assumptions can lead to big problems.</p>
      <p class="body">In a poll conducted in a recent webinar[ii] where half of the participants indicated they were already using DITA, a full 70% indicated that they had no formal DITA training. Of those participants, nearly 60% were self-taught while the others had no training at all. It’s no wonder that dissatisfaction is the norm.</p>
      <h2 class="section">Selecting the best training for your needs</h2>
      <p class="body" style="margin-top:6px">There are many training options available to learn about DITA. Selecting the best training for your team entails examining what it is you need to learn. Most DITA training courses cover the features and walk you through the structures and mechanics of the standard. These courses demonstrate how to markup content, but will often not teach you how to rethink and restructure your content to take advantage of DITA’s features. Consider the differences between structured writing and structured markup.</p>
      <table class="compare">
        <thead><tr><th class="sw" colspan="2">Structured Writing</th><th class="sm" colspan="2">Structured Markup</th></tr></thead>
        <tbody>
          <tr><td class="tick">√</td><td>Coined by Martin Greer in the 1960’s as a means of analyzing, organizing, and presenting information for optimal human consumption</td><td class="tick">√</td><td>Allows authors to markup words, phrases, and sections of content for presentation and for meaning for consumption by machines</td></tr>
          <tr><td class="tick">√</td><td>Promotes patterns for format and syntax that become easily recognizable and predictable</td><td class="tick">√</td><td>Is validated using standard sets of rules that specify consistent and predictable patterns</td></tr>
          <tr><td class="tick">√</td><td>Relies on consistently labelling and chunking information into easily scannable text</td><td class="tick">√</td><td>Specifies what content goes where but does not limit or restrict how the content is written</td></tr>
          <tr><td class="tick">√</td><td>Introduces universal information typing based on intended reader response</td><td class="tick">√</td><td>Provides a rich underlying metadata layer for capturing properties related to the content</td></tr>
        </tbody>
      </table>
      <p class="table-note">Table reproduced from “Scaling Team Output with Modular Content Practices[iii]”.</p>
      <h2 class="section">Continuous collaborative learning</h2>
      <p class="body" style="margin-top:6px">Organizations that wisely invest in comprehensive training for their writing teams also recognize the importance of continuous learning and recurring training. To stay on top of knowledge sharing in your team, consider the following collaboration activities:</p>
      <ul class="checklist">
        <li><svg width="11" height="11" viewBox="0 0 11 11" aria-hidden="true"><rect x=".5" y=".5" width="10" height="10" fill="none" stroke="#555"/><path d="M2.5 5.5l2 2 4-5" fill="none" stroke="#333" stroke-width="1.4"/></svg>Schedule regular checkpoints where your team discusses what they’ve learned with other members of the team.</li>
        <li><svg width="11" height="11" viewBox="0 0 11 11" aria-hidden="true"><rect x=".5" y=".5" width="10" height="10" fill="none" stroke="#555"/><path d="M2.5 5.5l2 2 4-5" fill="none" stroke="#333" stroke-width="1.4"/></svg>Assign different members of your team to research and present best practices at regularly scheduled lunch-and-learn sessions.</li>
        <li><svg width="11" height="11" viewBox="0 0 11 11" aria-hidden="true"><rect x=".5" y=".5" width="10" height="10" fill="none" stroke="#555"/><path d="M2.5 5.5l2 2 4-5" fill="none" stroke="#333" stroke-width="1.4"/></svg>Attend webinars and seminars on best practices as a group and then debrief together to discuss aspects that should be incorporated into your day-to-day work.</li>
        <li><svg width="11" height="11" viewBox="0 0 11 11" aria-hidden="true"><rect x=".5" y=".5" width="10" height="10" fill="none" stroke="#555"/><path d="M2.5 5.5l2 2 4-5" fill="none" stroke="#333" stroke-width="1.4"/></svg>Review and update your content standards regularly as a team to keep your procedures and guidelines current and relevant.</li>
        <li><svg width="11" height="11" viewBox="0 0 11 11" aria-hidden="true"><rect x=".5" y=".5" width="10" height="10" fill="none" stroke="#555"/><path d="M2.5 5.5l2 2 4-5" fill="none" stroke="#333" stroke-width="1.4"/></svg>Pair up senior members of your team with new or junior members for regular mentoring and coaching.</li>
      </ul>
    </div>
    <footer class="footer">
      <svg width="575" height="50" viewBox="0 0 575 50" aria-hidden="true">
        <polygon points="0,8 195,8 207,28 575,28 575,50 0,50" fill="var(--navy)"/>
        <polygon points="575,32 221,32 233,50 575,50" fill="var(--sky)"/>
      </svg>
      <span class="footer-page" style="left:42px">PAGE 11 OF 10</span>
      <span class="footer-contact" style="right:30px">Phone: +1 (555) 014-2290 &nbsp;|&nbsp; more-info@brightquillpages.com</span>
    </footer>
  </section>

</main>
</body>
</html>
```